Need A Modern Website Design For ADSL2+ Provider

AIM: To sell affordable combined ADSL2+ Unlimited & phone line rentals to residential customers.

TYPE: This project is for DESIGN only (no code)

Source Files: I need all source files, fonts, images to be provided in ZIP format.

Logo: Existing (attached)

-Corporate Colours-
Black & Red (Same as Logo)
Others colours are fine as long as it looks corporate and modern.

-Pages-
Need another page to display our pricing plan

(1)Homepage Design
(2)Page to display our plans (needs to be in tables)
Example: http://lnkrip.example/QwTr8k

-Pricing Plan-
(1) $59.95 / Month (Metro / City Areas)
(2) $79.95 / Month (Outside City Areas / Rural Areas)
Detailed Pricing plans is in PDF attached
Updates

Just letting everyone know we have picked a designer, thank you for all you submissions.

Target Market(s)

Both male & female, Young & Old

Industry/Entity Type

Residential

Requirements
Must have
• + Graphic banner on the home page that shows our ADSL2+ combo plan for ADSL2+ Unlimited & Phone Line Rental for only $59.95

+ A box to allow customers to login to their account (username & password + login button)

+ Clearly display contact number
+ Button to sign up
+ Button to check service availability something like https://checkline.vobbern.example/wizard/

+ Button for Live Chat
+ Navigation menu
+ Social media icons Pagebook, Zentra +, Chirpel
+ Minimal text on homepage
+ Corporate & Friendly
Nice to have
• + Effective use of icons with corporate colours
+ Effective use of stockphotos
(use of people in photos would be nice)

+ Effective use of graphics to navigate people through the site and inform customers of specials,etc.
Should not have
• + Cluttered
+ Don’t want long scrolling homepage
+ Don’t want too much text on homepage 500 words is the estimate max.

```html
<!DOCTYPE html>
<html lang="en">
<head>
<meta charset="utf-8">
<title>Korven – ADSL2+ Unlimited &amp; Phone Line Rental</title>
<link rel="stylesheet" href="https://fonts.googleapis.com/css2?family=Bebas+Neue&family=Oswald:wght@300;400;500&family=Roboto+Condensed:wght@300;400&family=Arimo:wght@400;700&display=swap">
<style>
:root{
  --red:#f0392b;
  --red-dark:#c9231a;
  --black:#0c0c0c;
  --ink:#111;
  --grey-band:#e4e4e4;
  --grey-box:#e2e2e2;
  --orange:#f7a31a;
  --white:#fff;
}
*{box-sizing:border-box;margin:0;padding:0}
html,body{width:1145px;height:1200px;overflow:hidden;background:var(--white);font-family:"Arimo",Arial,sans-serif;color:var(--ink)}
.page{position:relative;width:1145px;height:1200px;overflow:hidden}

/* header */
.site-header{position:absolute;left:0;top:0;width:1145px;height:91px;background:var(--white);border-bottom:3px solid var(--red)}
.brand{position:absolute;left:53px;top:24px;display:flex;align-items:center;gap:10px}
.brand-dot{width:44px;height:44px;border-radius:50%;background:var(--black)}
.brand-name{font-family:"Oswald",sans-serif;font-weight:400;font-size:34px;letter-spacing:2px;color:var(--black)}
.header-actions{position:absolute;left:506px;top:42px;display:flex;gap:6px}
.pill{height:33px;padding:0 11px;border-radius:9px;background:var(--red);color:var(--white);font-family:"Bebas Neue",sans-serif;font-size:27px;line-height:35px;text-transform:uppercase}
.call{position:absolute;right:14px;top:14px;text-align:right;color:var(--black)}
.call-label{font-family:"Bebas Neue",sans-serif;font-size:19px;line-height:20px}
.call-number{font-family:"Bebas Neue",sans-serif;font-size:46px;line-height:46px;letter-spacing:1px}

/* nav */
.main-nav{position:absolute;left:0;top:93px;width:1145px;height:49px;background:linear-gradient(#1c1c1c,#000)}
.main-nav a{position:absolute;top:0;height:49px;line-height:49px;color:var(--white);font-family:"Roboto Condensed",sans-serif;font-size:18px;text-decoration:none}
.main-nav .active{left:29px;width:101px;text-align:center;background:var(--red)}

/* hero */
.hero{position:absolute;left:0;top:142px;width:1145px;height:363px;background:linear-gradient(90deg,#5a5a5a,#8a8a8a 40%,#3a3a3a 70%,#2a2a2a)}
.hero-photo{position:absolute;left:0;top:0;width:705px;height:363px;background:radial-gradient(circle at 60% 40%,#9a9a9a,#4a4a4a 70%,#333)}
.hero-panel{position:absolute;left:705px;top:0;width:402px;height:363px}
.hero-copy{position:absolute;left:705px;top:22px;width:402px;text-align:center}
.hero-title{font-family:"Oswald",sans-serif;font-weight:500;font-size:45px;line-height:52px;color:#d8d8d8}
.hero-price{margin-top:10px;font-size:28px;color:var(--orange)}
.hero-cta{display:inline-block;margin-top:22px;width:222px;height:42px;line-height:38px;border:2px solid var(--red-dark);border-radius:6px;background:linear-gradient(#f4513f,#d62a1c);color:var(--white);font-weight:700;font-size:16px;letter-spacing:.5px}

/* content */
.content{position:absolute;left:0;top:505px;width:1145px;height:525px;background:linear-gradient(#dfe2e6,#fff 14%,#fff 84%,#e2e2e2)}
.section-title{position:absolute;font-family:"Roboto Condensed",sans-serif;font-weight:300;font-size:35px;letter-spacing:-.5px;color:var(--black)}
.login-box{position:absolute;left:37px;top:99px;width:519px;height:75px;border-radius:10px;background:var(--grey-box)}
.field{position:absolute;top:23px;width:175px;height:31px;border:1px solid #d0d0d0;border-radius:6px;background:var(--white);padding-left:12px;font-size:14px;line-height:29px;color:#555}
.login-btn{position:absolute;left:402px;top:23px;width:96px;height:31px;border-radius:4px;background:linear-gradient(#333,#000);color:var(--white);font-size:15px;line-height:31px;text-align:center}
.about-text{position:absolute;left:43px;top:294px;width:520px;font-size:14.3px;line-height:17px;color:var(--black)}
.more-link{position:absolute;left:43px;top:418px;font-size:14px;color:var(--red)}

.plan-card{position:absolute;top:109px;width:227px;height:299px;border-radius:12px;overflow:hidden;background:linear-gradient(#ffe24a,#fdb81e 55%,#f98d12);box-shadow:-8px 6px 14px rgba(0,0,0,.25);text-align:center;color:var(--white)}
.plan-corner{position:absolute;left:0;top:0}
.plan-name{margin-top:16px;font-family:"Oswald",sans-serif;font-weight:400;font-size:45px;line-height:54px;color:#151515}
.plan-price{font-family:"Oswald",sans-serif;font-weight:300;font-size:38px;line-height:46px}
.plan-perk{margin-top:4px;font-weight:700;font-size:20px;line-height:21px}
.plan-rate{margin-top:12px;font-family:"Oswald",sans-serif;font-weight:300;font-size:22px;color:#2a1a00;padding-bottom:8px;border-bottom:1px solid #c8720e;margin-left:10px;margin-right:10px}
.plan-ld{margin-top:8px;font-family:"Oswald",sans-serif;font-weight:300;color:#2a1a00;font-size:22px;line-height:24px}
.plan-ld small{display:block;font-size:16px;line-height:18px}
.plan-link{position:absolute;top:422px;display:flex;align-items:center;gap:10px;font-family:"Oswald",sans-serif;font-weight:300;font-size:17px;color:var(--red)}

/* footer */
.social-bar{position:absolute;left:0;top:1047px;width:1145px;height:47px;background:#141414;display:flex;justify-content:center;align-items:center;gap:8px}
.social-dot{width:32px;height:32px;border-radius:50%;background:#e6e6e6}
.site-footer{position:absolute;left:0;top:1094px;width:1145px;height:106px;background:var(--grey-band);text-align:center}
.footer-links{margin-top:22px;font-size:14.5px;color:var(--black)}
.footer-links span{margin:0 6px}
.copyright{margin-top:10px;font-size:12.5px;color:var(--red)}
</style>
</head>
<body>
<div class="page">
  <header class="site-header">
    <div class="brand"><span class="brand-dot"></span><span class="brand-name">KORVEN</span></div>
    <div class="header-actions">
      <span class="pill">Sign Up</span>
      <span class="pill">Check Availablity</span>
      <span class="pill">Live Chat</span>
    </div>
    <div class="call">
      <div class="call-label">To find out more or join call</div>
      <div class="call-number">1300 55 18 90</div>
    </div>
  </header>

  <nav class="main-nav">
    <a class="active" href="#">Home</a>
    <a href="#" style="left:180px">About us</a>
    <a href="#" style="left:328px">Products and Services</a>
    <a href="#" style="left:580px">Pricing</a>
    <a href="#" style="left:710px">Specials</a>
    <a href="#" style="left:851px">Contact Us</a>
  </nav>

  <section class="hero">
    <div class="hero-photo" role="img" aria-label="Stock photo of a businessman in a suit working on a laptop in front of a circuit board backdrop"></div>
    <svg class="hero-panel" width="402" height="363" viewBox="0 0 402 363" aria-hidden="true">
      <polygon points="0,0 402,0 402,280 201,340 0,280" fill="#111"/>
    </svg>
    <div class="hero-copy">
      <h1 class="hero-title">ADSL2+ Unlimited<br>&amp; Phone Line RentaL</h1>
      <p class="hero-price">for only $59.95</p>
      <span class="hero-cta">SUBSCRIBE PLAN</span>
    </div>
  </section>

  <main class="content">
    <h2 class="section-title" style="left:44px;top:47px">USER LOGIN</h2>
    <div class="login-box">
      <span class="field" style="left:17px">username</span>
      <span class="field" style="left:207px">password</span>
      <span class="login-btn">LOGIN</span>
    </div>

    <h2 class="section-title" style="left:44px;top:232px">ABOUT KORVEN</h2>
    <p class="about-text">Korven’s Combo2+ broadband and telephone plan is for Unlimited Broad band, line rental and for all calls which go over those lines. The plan requires the ADSL 2+ service, the telephone line and the pre-selection service (long distance and fixed to mobile calls) to be bundled. The service comes with a Wifi modem which is free but it will cost you $24.95 for delivery and handling and is a mandatory part of the service.</p>
    <a class="more-link">more info</a>

    <h2 class="section-title" style="left:651px;top:47px">COMBO2+ PLANS</h2>

    <div class="plan-card" style="left:663px">
      <svg class="plan-corner" width="62" height="62" viewBox="0 0 62 62" aria-hidden="true"><polygon points="0,0 62,0 0,62" fill="#e8231a"/><text x="16" y="38" transform="rotate(-45 16 38)" font-family="Arimo,sans-serif" font-size="9" font-weight="700" fill="#fff">ON NET</text></svg>
      <div class="plan-name">Metro</div>
      <div class="plan-price">$59.95</div>
      <div class="plan-perk">Free Set Up and<br>WIFI Modem</div>
      <div class="plan-rate">.18c per Local Calls</div>
      <div class="plan-ld">.29c / minute<small>Long Distance Calls</small></div>
    </div>
    <div class="plan-card" style="left:891px">
      <svg class="plan-corner" width="62" height="62" viewBox="0 0 62 62" aria-hidden="true"><polygon points="0,0 62,0 0,62" fill="#e8231a"/><text x="13" y="40" transform="rotate(-45 13 40)" font-family="Arimo,sans-serif" font-size="9" font-weight="700" fill="#fff">OFF NET</text></svg>
      <div class="plan-name">Regional</div>
      <div class="plan-price">$79.95</div>
      <div class="plan-perk">Free Set Up and<br>WIFI Modem</div>
      <div class="plan-rate">.18c per Local Calls</div>
      <div class="plan-ld">.29c / minute<small>Long Distance Calls</small></div>
    </div>

    <a class="plan-link" style="left:665px"><svg width="20" height="20" viewBox="0 0 20 20" aria-hidden="true"><circle cx="10" cy="10" r="9" fill="#f7a31a"/><polygon points="8,6 14,10 8,14" fill="#c9231a"/></svg>SUBSCRIBE PLAN NOW</a>
    <a class="plan-link" style="left:896px"><svg width="20" height="20" viewBox="0 0 20 20" aria-hidden="true"><circle cx="10" cy="10" r="9" fill="#f7a31a"/><polygon points="8,6 14,10 8,14" fill="#c9231a"/></svg>SUBSCRIBE PLAN NOW</a>
  </main>

  <div class="social-bar" aria-label="Social links: Chirpel, Pagebook, Zentra +, Linkora, news feed">
    <span class="social-dot"></span><span class="social-dot"></span><span class="social-dot"></span><span class="social-dot"></span><span class="social-dot"></span>
  </div>

  <footer class="site-footer">
    <div class="footer-links">ABOUT US<span>·</span>PRODUCTS AND SERVICES<span>·</span>PRICING<span>·</span>SPECIALS<span>·</span>CONTACT US</div>
    <div class="copyright">© Copyright 2013 Korven. All Rights Reserved</div>
  </footer>
</div>
</body>
</html>
```